Web Site Design for a Finance (lending) Company

We are opening a new subsidiary that focuses on lending money in the real estate industry. We need a web site designed to represent the business.

The business is lending money to real estate investors. A typical client/borrower will be looking to borrow money to buy a house, renovate it and then sell it at a profit, all within 12 months or less.

Company name is RTV Finance. Our logo is attached.

Attached is a general outline for the web site. We're working on writing more text for each page but this should give you enough to get started with some ideas.

Competitor web site that I like a lot (as an example): https://dorvaleqcapital.example/. Many of the general items on this site match what we will need (description of loan programs, FAQ)

Target Market(s)

Real estate investors (generally individuals or small companies with just a few people) who are buying homes, renovating them and then selling them at a profit.

Industry/Entity Type

Finance

Coding

Coded - Design and coding required

Number of Pages Required

5+ page

Colors

Designer to choose colors to be used in the design.

Requirements
Must have
• Minimalist design. Clean lines without too much clutter. Some stock photography is ok but the photos should not be distracting. They should almost fade in to the background so that user can focus on the key information about what our company does instead. We are a finance company, not a design company, so the information about our products will be more interesting to site visitors than the art.
• Some minimalist examples from Snapboard:
• https://www.snapboardia.example/explore/minimalist-web-design/
Nice to have
• If you search in zoovle for "hard money lenders" you will find many examples of web sites from our competition. I have provided a link above to competitor web site that I like a lot.
• I have attached our logo in EPS format. Logo is green. Web site doesn't have to be green but it should be of a color that will work well with the logo.

```html
<!DOCTYPE html>
<html lang="en">
<head>
<meta charset="utf-8">
<title>RTV Finance</title>
<link rel="stylesheet" href="https://fonts.googleapis.com/css2?family=Roboto:wght@400;500;700&family=Open+Sans:ital,wght@0,400;0,600;1,400&display=swap">
<style>
:root{
  --green:#0d5a3b;
  --green-dark:#0a4a30;
  --ink:#1f1f1f;
  --text:#555;
  --muted:#8a8a8a;
  --line:#d4d4d4;
  --light:#f4f4f4;
  --footer:#1b1b1b;
  --footer-text:#e6e6e6;
  --testimonial:#a3a3a8;
}
*{box-sizing:border-box;margin:0;padding:0}
html,body{width:1200px;height:2590px;overflow:hidden}
body{position:relative;font-family:"Open Sans",Arial,sans-serif;color:var(--text);background:#fff}
h2.section-title{font-family:"Roboto",Arial,sans-serif;font-weight:500;font-size:27px;color:var(--ink);text-align:center;letter-spacing:.3px}

/* header */
.site-header{position:absolute;left:0;top:0;width:1200px;height:92px;background:#fff}
.brand{position:absolute;left:100px;top:24px;display:flex;align-items:center;gap:10px}
.brand-mark{width:26px;height:26px;background:var(--green)}
.brand-name{font-family:"Roboto",Arial,sans-serif;font-weight:700;font-size:25px;color:var(--green)}
.main-nav{position:absolute;right:100px;top:28px;display:flex;align-items:center;gap:34px;font-family:"Roboto",Arial,sans-serif;font-weight:500;font-size:15px;color:var(--ink)}
.main-nav .active{color:var(--green)}
.login-btn{background:var(--green);color:#fff;padding:10px 14px;display:flex;align-items:center;gap:6px;font-size:15px}

/* hero */
.hero{position:absolute;left:0;top:92px;width:1200px;height:530px;overflow:hidden}
.hero-photo{position:absolute;inset:0;background:linear-gradient(180deg,#9fb8cf 0%,#c4d3df 28%,#5f7a4a 45%,#4b6d2f 62%,#6a8a3e 100%)}
.hero-title{position:absolute;left:0;top:160px;width:1200px;text-align:center;font-family:"Roboto",Arial,sans-serif;font-weight:700;font-size:46px;line-height:64px;color:#fff;text-shadow:0 2px 6px rgba(0,0,0,.35)}
.dots{position:absolute;display:flex;gap:4px}
.dots span{width:11px;height:11px;border-radius:50%;border:1.5px solid #fff}
.dots span.on{background:#fff}
.hero-edge{position:absolute;left:0;top:380px}

/* welcome */
.welcome-title{position:absolute;top:648px;width:1200px}
.welcome-text{position:absolute;left:190px;top:704px;width:820px;text-align:center;font-size:12.5px;line-height:25px;color:var(--text)}
.loan-card{position:absolute;top:805px;width:470px}
.icon-ring{position:absolute;left:0;top:0;border:1.5px solid #666;border-radius:50%;display:flex;align-items:center;justify-content:center;background:#fff}
.loan-card .icon-ring{width:124px;height:124px}
.loan-card h3{position:absolute;left:150px;top:10px;font-family:"Roboto",Arial,sans-serif;font-weight:500;font-size:19px;color:var(--ink)}
.loan-points{position:absolute;left:150px;top:48px;list-style:none;font-size:11.5px;color:var(--text)}
.loan-points li{display:flex;align-items:center;gap:9px;height:29px}

/* why borrow */
.why{position:absolute;left:0;top:1041px;width:1200px;height:474px;background:var(--light)}
.why .section-title{position:absolute;top:66px;width:1200px}
.feature{position:absolute;width:340px;height:90px}
.feature .icon-ring{width:87px;height:87px;border-color:#9a9a9a}
.feature h3{position:absolute;left:103px;top:6px;font-family:"Roboto",Arial,sans-serif;font-weight:500;font-size:19px;color:var(--ink)}
.feature p{position:absolute;left:103px;top:38px;width:220px;font-size:12px;line-height:24px;color:var(--muted)}

/* testimonial */
.testimonials{position:absolute;left:0;top:1515px;width:1200px;height:336px;background:var(--testimonial);overflow:hidden}
.testimonials .wedge{position:absolute;left:0;top:0}
.quote-mark{position:absolute;left:98px;top:32px}
.testimonials h2{position:absolute;left:98px;top:132px;font-family:"Roboto",Arial,sans-serif;font-weight:500;font-size:27px;line-height:37px;color:#fff}
.avatar{position:absolute;left:527px;top:40px;width:100px;height:100px;border-radius:50%;border:4px solid #fff;background:radial-gradient(circle at 50% 40%,#c9b8a8 0%,#8b8f98 55%,#5d6470 100%)}
.quote{position:absolute;left:525px;top:160px;width:580px;font-style:italic;font-size:15.5px;line-height:27px;color:#fff}
.quote-author{position:absolute;left:525px;top:267px;font-size:16px;font-weight:600;color:#fff}
.quote-author em{font-weight:600}

/* membership */
.membership-title{position:absolute;top:1930px;width:1200px}
.badges{position:absolute;left:100px;top:2006px;display:flex;gap:33px}
.badge{width:175px;height:83px;border:1.5px solid var(--line);display:flex;align-items:center;justify-content:center}
.badge span{display:block;width:110px;height:30px;background:#cfcfcf}

/* footer */
.footer-edge{position:absolute;left:0;top:2130px}
.site-footer{position:absolute;left:0;top:2235px;width:1200px;height:355px;background:var(--footer);color:var(--footer-text)}
.footer-brand{position:absolute;left:100px;top:115px;display:flex;align-items:center;gap:12px}
.footer-brand .brand-mark{width:34px;height:34px;background:var(--green)}
.footer-brand .brand-name{font-family:"Roboto",Arial,sans-serif;font-weight:500;font-size:33px;color:#bdbdbd}
.footer-col{position:absolute;top:62px}
.footer-col h4{font-family:"Roboto",Arial,sans-serif;font-weight:500;font-size:16px;color:#fff;margin-bottom:20px;letter-spacing:.2px}
.quick-links{list-style:none;font-size:12.5px}
.quick-links li{height:30px}
.newsletter p{font-size:12.5px;line-height:22px;width:200px}
.newsletter .email-field{margin-top:14px;width:253px;height:35px;background:#fff;color:#666;font-size:12px;padding:9px 12px}
.newsletter .subscribe{margin-top:16px;display:inline-block;background:var(--green);color:#fff;font-size:12px;font-weight:600;padding:10px 16px}
.contact-list{list-style:none;font-size:12.5px}
.contact-list li{display:flex;gap:16px;align-items:flex-start;margin-bottom:14px;line-height:20px}
.contact-list svg{flex:none;margin-top:3px}
.footer-rule{position:absolute;left:93px;top:286px;width:1012px;height:1px;background:#3a3a3a}
.copyright{position:absolute;left:93px;top:313px;font-size:12px}
.social{position:absolute;right:95px;top:306px;display:flex;gap:8px}
.social span{width:27px;height:27px;border:1.5px solid #ddd;border-radius:50%}
.livechat{position:absolute;left:1153px;top:2219px;width:47px;height:138px;background:var(--green);display:flex;align-items:center;justify-content:center}
.livechat span{transform:rotate(-90deg);color:#fff;font-family:"Roboto",Arial,sans-serif;font-weight:700;font-size:15px;white-space:nowrap;letter-spacing:.5px}
</style>
</head>
<body>

<header class="site-header">
  <div class="brand"><span class="brand-mark"></span><span class="brand-name">RTV Finance</span></div>
  <nav class="main-nav">
    <span class="active">HOME</span><span>ABOUT US</span><span>LOANS</span><span>RESOURCES</span><span>CONTACT US</span>
    <svg width="15" height="15" viewBox="0 0 16 16"><circle cx="6.5" cy="6.5" r="5" fill="none" stroke="#1f1f1f" stroke-width="2"/><path d="M10.5 10.5l4 4" stroke="#1f1f1f" stroke-width="2.2"/></svg>
    <span class="login-btn"><svg width="11" height="13" viewBox="0 0 11 13"><rect x="0" y="5" width="11" height="8" fill="#fff"/><path d="M2.5 5V3.5a3 3 0 0 1 6 0V5" fill="none" stroke="#fff" stroke-width="1.6"/></svg>LOGIN</span>
  </nav>
</header>

<section class="hero">
  <div class="hero-photo" role="img" aria-label="Brick family home on a green lawn with trees under a cloudy sky"></div>
  <h1 class="hero-title">Local real estate experts lending to<br>local real estate investors</h1>
  <div class="dots" style="left:571px;top:367px"><span class="on"></span><span></span><span></span><span></span></div>
  <svg class="hero-edge" width="1200" height="150" viewBox="0 0 1200 150">
    <polygon points="0,124 806,40 1200,86 1200,150 0,150" fill="var(--green)"/>
    <polygon points="0,146 806,54 1200,100 1200,150 0,150" fill="#fff"/>
  </svg>
</section>

<h2 class="section-title welcome-title">WELCOME TO RTV FINANCE</h2>
<p class="welcome-text">RTV Finance is a local business with local knowledge and strong industry relationships. A partner with a wide network who offers value added services. RTV has an established pool of experienced investors available for your real estate investment needs</p>

<div class="loan-card" style="left:100px">
  <div class="icon-ring"><svg width="54" height="54" viewBox="0 0 54 54"><circle cx="27" cy="27" r="27" fill="var(--green)"/><path d="M15 28l8 8 16-17" fill="none" stroke="#fff" stroke-width="6" stroke-linecap="round" stroke-linejoin="round"/></svg></div>
  <h3>Fix and Flip Loans</h3>
  <ul class="loan-points">
    <li><svg width="12" height="10" viewBox="0 0 12 10"><path d="M1 5l3.5 3.5L11 1.5" fill="none" stroke="var(--green)" stroke-width="2.4"/></svg>Description of the loan type, borrower requirements</li>
    <li><svg width="12" height="10" viewBox="0 0 12 10"><path d="M1 5l3.5 3.5L11 1.5" fill="none" stroke="var(--green)" stroke-width="2.4"/></svg>Loan terms table</li>
    <li><svg width="12" height="10" viewBox="0 0 12 10"><path d="M1 5l3.5 3.5L11 1.5" fill="none" stroke="var(--green)" stroke-width="2.4"/></svg>Why choose RTV</li>
    <li><svg width="12" height="10" viewBox="0 0 12 10"><path d="M1 5l3.5 3.5L11 1.5" fill="none" stroke="var(--green)" stroke-width="2.4"/></svg>Online application or Contact web form</li>
  </ul>
</div>
<div class="loan-card" style="left:637px">
  <div class="icon-ring"><svg width="40" height="58" viewBox="0 0 40 58"><rect width="40" height="58" fill="var(--green)"/><g fill="#fff"><rect x="6" y="7" width="7" height="7"/><rect x="17" y="7" width="7" height="7"/><rect x="28" y="7" width="7" height="7"/><rect x="6" y="19" width="7" height="7"/><rect x="17" y="19" width="7" height="7"/><rect x="28" y="19" width="7" height="7"/><rect x="6" y="31" width="7" height="7"/><rect x="17" y="31" width="7" height="7"/><rect x="28" y="31" width="7" height="7"/><rect x="15" y="44" width="10" height="14"/></g></svg></div>
  <h3>Commercial Hard Money Loans</h3>
  <ul class="loan-points">
    <li><svg width="12" height="10" viewBox="0 0 12 10"><path d="M1 5l3.5 3.5L11 1.5" fill="none" stroke="var(--green)" stroke-width="2.4"/></svg>Description of the loan type, borrower requirements</li>
    <li><svg width="12" height="10" viewBox="0 0 12 10"><path d="M1 5l3.5 3.5L11 1.5" fill="none" stroke="var(--green)" stroke-width="2.4"/></svg>Loan terms table</li>
    <li><svg width="12" height="10" viewBox="0 0 12 10"><path d="M1 5l3.5 3.5L11 1.5" fill="none" stroke="var(--green)" stroke-width="2.4"/></svg>Why choose RTV</li>
    <li><svg width="12" height="10" viewBox="0 0 12 10"><path d="M1 5l3.5 3.5L11 1.5" fill="none" stroke="var(--green)" stroke-width="2.4"/></svg>Online application or Contact web form</li>
  </ul>
</div>

<section class="why">
  <h2 class="section-title">WHY BORROW FROM RTV</h2>

  <div class="feature" style="left:100px;top:156px">
    <div class="icon-ring"><svg width="28" height="30" viewBox="0 0 28 30"><circle cx="14" cy="8" r="7" fill="var(--green)"/><path d="M1 30c0-9 5-13 13-13s13 4 13 13z" fill="var(--green)"/></svg></div>
    <h3>Experts</h3><p>Nam libero tempore, cum solu tano bis est eligendi.</p>
  </div>
  <div class="feature" style="left:459px;top:156px">
    <div class="icon-ring"><svg width="34" height="32" viewBox="0 0 34 32"><path d="M33 1L1 14l10 4 2 12 5-8 9 5z" fill="var(--green)"/></svg></div>
    <h3>Fast Approval</h3><p>Nam libero tempore, cum solu tano bis est eligendi.</p>
  </div>
  <div class="feature" style="left:815px;top:156px">
    <div class="icon-ring"><svg width="36" height="30" viewBox="0 0 36 30"><rect x="12" y="1" width="12" height="6" fill="none" stroke="var(--green)" stroke-width="3"/><rect x="0" y="7" width="36" height="23" rx="3" fill="var(--green)"/><rect x="9" y="7" width="2" height="23" fill="#fff"/><rect x="25" y="7" width="2" height="23" fill="#fff"/></svg></div>
    <h3>Professional</h3><p>Nam libero tempore, cum solu tano bis est eligendi.</p>
  </div>
  <div class="feature" style="left:100px;top:294px">
    <div class="icon-ring"><svg width="38" height="30" viewBox="0 0 38 30"><circle cx="8" cy="7" r="5" fill="var(--green)"/><circle cx="30" cy="7" r="5" fill="var(--green)"/><circle cx="19" cy="9" r="6.5" fill="var(--green)"/><path d="M0 22c0-6 3-9 8-9s8 3 8 9zM22 22c0-6 3-9 8-9s8 3 8 9z" fill="var(--green)"/><path d="M8 30c0-9 4-13 11-13s11 4 11 13z" fill="var(--green)"/></svg></div>
    <h3>Partner</h3><p>Nam libero tempore, cum solu tano bis est eligendi.</p>
  </div>
  <div class="feature" style="left:459px;top:294px">
    <div class="icon-ring"><svg width="34" height="32" viewBox="0 0 34 32"><rect x="2" y="5" width="25" height="25" rx="3" fill="none" stroke="var(--green)" stroke-width="3.5"/><path d="M8 16l7 7L32 4" fill="none" stroke="var(--green)" stroke-width="4.5"/></svg></div>
    <h3>Selective</h3><p>Nam libero tempore, cum solu tano bis est eligendi.</p>
  </div>
  <div class="feature" style="left:815px;top:294px">
    <div class="icon-ring"><svg width="38" height="24" viewBox="0 0 38 24"><rect width="38" height="24" fill="var(--green)"/><rect x="4" y="4" width="30" height="16" fill="none" stroke="#fff" stroke-width="1.5"/><circle cx="19" cy="12" r="6" fill="#fff"/><rect x="17.5" y="8" width="3" height="8" fill="var(--green)"/></svg></div>
    <h3>Competitive rates &amp; fees</h3><p>Nam libero tempore, cum solu tano bis est eligendi.</p>
  </div>
</section>

<section class="testimonials">
  <svg class="wedge" width="525" height="336" viewBox="0 0 525 336"><polygon points="0,0 522,0 159,336 0,190" fill="var(--green)"/></svg>
  <svg class="quote-mark" width="88" height="76" viewBox="0 0 88 76"><path d="M0 76V38C0 14 10 2 34 0v14C20 16 16 24 16 34h20v42zM52 76V38C52 14 62 2 86 0v14C72 16 68 24 68 34h20v42z" fill="#fff"/></svg>
  <h2>CLIENT<br>TESTIMONIALS</h2>
  <div class="avatar" role="img" aria-label="Portrait photo of the client giving the testimonial"></div>
  <p class="quote">At vero eos et accusamus et iusto odio dignissimos ducimus qui blanditii praesen tium voluptatum deleniti atque corrupti quos dolores et quas molestias excepturi sint occaecati cupiditate non provident, similique sunt..</p>
  <p class="quote-author">- JOHN DOE <em>(Manager)</em></p>
  <div class="dots" style="left:1056px;top:285px"><span class="on"></span><span></span><span></span></div>
</section>

<h2 class="section-title membership-title">INDUSTRY MEMBERSHIP</h2>
<div class="badges">
  <div class="badge"><span></span></div>
  <div class="badge"><span></span></div>
  <div class="badge"><span></span></div>
  <div class="badge"><span></span></div>
  <div class="badge"><span></span></div>
</div>

<svg class="footer-edge" width="1200" height="110" viewBox="0 0 1200 110">
  <polygon points="0,60 397,90 1200,0 1200,12 397,102 0,72" fill="var(--green)"/>
  <polygon points="0,72 397,102 1200,12 1200,110 0,110" fill="var(--footer)"/>
</svg>

<footer class="site-footer">
  <div class="footer-brand"><span class="brand-mark"></span><span class="brand-name">RTV Finance</span></div>

  <div class="footer-col" style="left:426px">
    <h4>QUICK LINKS</h4>
    <ul class="quick-links"><li>Home</li><li>About Us</li><li>Loans</li><li>Resources</li><li>Contact Us</li></ul>
  </div>

  <div class="footer-col newsletter" style="left:597px">
    <h4>NEWSLETTER SUBSCRIPTION</h4>
    <p>Register your Email Address to get Information about us</p>
    <div class="email-field">Email Address</div>
    <span class="subscribe">SUBSCRIBE</span>
  </div>

  <div class="footer-col" style="left:929px">
    <h4>CONTACT US</h4>
    <ul class="contact-list">
      <li><svg width="12" height="15" viewBox="0 0 12 15"><path d="M6 0a6 6 0 0 1 6 6c0 4-6 9-6 9S0 10 0 6a6 6 0 0 1 6-6z" fill="#fff"/><circle cx="6" cy="6" r="2.2" fill="var(--footer)"/></svg><span>2840 Larkspur Lane, Fenwick<br>MO 64100</span></li>
      <li><svg width="14" height="14" viewBox="0 0 14 14"><path d="M3 0l3 3-2 2c1 2 3 4 5 5l2-2 3 3-2 3C6 14 0 8 0 3z" fill="#fff"/></svg><span>1 888 888 8888</span></li>
      <li><svg width="15" height="14" viewBox="0 0 15 14"><rect x="0" y="4" width="15" height="10" fill="#fff"/><rect x="3" y="0" width="9" height="5" fill="none" stroke="#fff" stroke-width="1.5"/><rect x="3" y="7" width="9" height="4" fill="var(--footer)"/></svg><span>1 222 222 2222</span></li>
      <li><svg width="15" height="11" viewBox="0 0 15 11"><rect width="15" height="11" fill="#fff"/><path d="M0 0l7.5 6L15 0" fill="none" stroke="var(--footer)" stroke-width="1.5"/></svg><span>info@rtvfinance.example</span></li>
    </ul>
  </div>

  <div class="footer-rule"></div>
  <p class="copyright">Copyrights © 2017,&nbsp; RTV Finance&nbsp; All rights reserved.</p>
  <div class="social"><span></span><span></span><span></span><span></span></div>
</footer>

<div class="livechat"><span>LIVECHAT</span></div>

</body>
</html>
```